Carpentry framing business card and logo design

We need a logo that works well with baseball caps, tee shirts and sweat shirts. We are a carpentry framing company specializing in apartment complexes and large residential communities. We work in what is known as the tri state area southeastern Pennsylvania , New Jersey and northern Delaware . We would like to see die signs using the old English letter M and royal blue colors. Also we stress OSHA compliance and safety.

Industry/Entity Type

Residential

Contact Information for Business Card

Valdrick Construction Co Inc
4870 Quillford Lane
Brenford PA 19087
Dale Valdrick
dale1valdrick@norvexmail.com
267-815-0926

```html
<!DOCTYPE html>
<html lang="en">
<head>
<meta charset="UTF-8">
<title>Valdrick Construction Co Inc — Business Card</title>
<link href="https://fonts.googleapis.com/css2?family=Jost:wght@400;500;700&display=swap" rel="stylesheet">
<style>
  :root {
    --royal-navy: #1f2f6e;
    --ink: #2a2f45;
    --card-white: #f6f5f1;
    --backdrop: #d9d6d0;
  }
  * { margin: 0; padding: 0; box-sizing: border-box; }
  html, body {
    width: 1200px;
    height: 800px;
    overflow: hidden;
    background: var(--backdrop);
    font-family: "Jost", "Futura", sans-serif;
  }
  .business-card {
    position: absolute;
    left: 180px;
    top: 160px;
    width: 840px;
    height: 480px;
    background: var(--card-white);
    box-shadow: 0 6px 18px rgba(0, 0, 0, 0.18);
  }
  .accent-bar {
    position: absolute;
    left: 0;
    top: 74px;
    width: 24px;
    height: 286px;
    background: var(--royal-navy);
  }
  .holder-name {
    position: absolute;
    left: 96px;
    top: 168px;
    font-size: 42px;
    font-weight: 700;
    color: var(--royal-navy);
    letter-spacing: 0.3px;
    white-space: nowrap;
  }
  .street-address {
    position: absolute;
    left: 98px;
    top: 262px;
    font-size: 17px;
    line-height: 1.15;
    font-weight: 400;
    font-style: normal;
    color: var(--ink);
  }
  .contact-list {
    position: absolute;
    left: 98px;
    top: 318px;
    list-style: none;
    font-size: 17px;
    font-weight: 400;
    color: var(--ink);
  }
  .contact-item {
    display: flex;
    align-items: center;
    gap: 10px;
    height: 30px;
    white-space: nowrap;
  }
  .contact-icon {
    width: 18px;
    height: 18px;
    flex: none;
  }
  .company-mark {
    position: absolute;
    left: 590px;
    top: 110px;
    width: 200px;
    display: flex;
    flex-direction: column;
    align-items: center;
    gap: 14px;
  }
  .company-mark-square {
    width: 96px;
    height: 96px;
    background: var(--royal-navy);
  }
  .company-name {
    font-size: 20px;
    font-weight: 500;
    line-height: 1.2;
    text-align: center;
    color: var(--royal-navy);
  }
</style>
</head>
<body>
  <section class="business-card">
    <div class="accent-bar"></div>

    <h1 class="holder-name">Dale Valdrick</h1>

    <address class="street-address">
      4870 Quillford Lane<br>
      Brenford PA 19087
    </address>

    <ul class="contact-list">
      <li class="contact-item">
        <svg class="contact-icon" viewBox="0 0 18 18" aria-hidden="true">
          <rect x="1.5" y="3.5" width="15" height="11" fill="none" stroke="#2a2f45" stroke-width="1.5"/>
          <polyline points="1.5,3.5 9,10 16.5,3.5" fill="none" stroke="#2a2f45" stroke-width="1.5"/>
        </svg>
        <span class="contact-email">dale1valdrick@norvexmail.com</span>
      </li>
      <li class="contact-item">
        <svg class="contact-icon" viewBox="0 0 18 18" aria-hidden="true">
          <rect x="4.5" y="1" width="9" height="16" rx="1.5" fill="none" stroke="#2a2f45" stroke-width="1.5"/>
          <line x1="7.5" y1="14.2" x2="10.5" y2="14.2" stroke="#2a2f45" stroke-width="1.3"/>
        </svg>
        <span class="contact-phone">267-815-0926</span>
      </li>
    </ul>

    <div class="company-mark">
      <div class="company-mark-square"></div>
      <p class="company-name">Valdrick<br>Construction Co Inc</p>
    </div>
  </section>
</body>
</html>
```